Modern Verdell Tree Care Website

I need a website for a full service Tree Care company. The company provides tree pruning, tree removal, tree preservation, emergency services, stump grinding, and emergency tree services.

Target Market(s)

Customers that need tree services

Industry/Entity Type

Landscaping, Tree Services

Coding

Coded - Design and coding required

Number of Pages Required

5+ page

Font styles to use
Sans Serif

Requirements
Must have
• Good clean design that showcases the services the company provides.
Nice to have
• Services page; contact form, blog, home page, about page

```html
<!DOCTYPE html>
<html lang="en">
<head>
<meta charset="utf-8">
<title>Verdell Tree Care</title>
<link href="https://fonts.googleapis.com/css2?family=Open+Sans:wght@400;600;700;800&family=Roboto:wght@300;400;500&display=swap" rel="stylesheet">
<style>
:root{
  --green:#8dc63f;
  --slate:#4b6670;
  --slate-dark:#3d5a66;
  --ink:#111111;
  --muted:#6b6b6b;
  --mint:#f4fae8;
  --orange:#f39200;
  --white:#ffffff;
  --black:#000000;
}
*{margin:0;padding:0;box-sizing:border-box}
html,body{width:1200px;height:4002px;overflow:hidden}
body{position:relative;background:var(--white);font-family:'Roboto',sans-serif;color:var(--ink)}
.abs{position:absolute}
.heading{font-family:'Open Sans',sans-serif;font-weight:800;text-transform:uppercase;letter-spacing:.5px;line-height:1}
.heading .accent{color:var(--green)}
.btn{position:absolute;background:var(--slate);color:var(--white);font-family:'Roboto',sans-serif;font-weight:500;font-size:14px;text-transform:uppercase;display:flex;align-items:center;justify-content:center;width:181px;height:42px}

/* header */
.site-header{top:0;left:0;width:1200px;height:101px;background:var(--white)}
.brand{left:110px;top:28px;display:flex;align-items:center;gap:12px}
.brand-square{width:40px;height:40px;background:var(--green)}
.brand-name{font-family:'Open Sans',sans-serif;font-weight:700;font-size:21px;color:var(--slate);line-height:1;white-space:nowrap}
.top-phone{left:923px;top:8px;display:flex;align-items:center;gap:10px;font-family:'Open Sans',sans-serif;font-weight:600;font-size:15px}
.icon-box{width:31px;height:31px;background:var(--orange);display:flex;align-items:center;justify-content:center}
.nav-bar{left:375px;top:53px;width:825px;height:48px}
.nav-links{left:444px;top:53px;height:48px;display:flex;align-items:center;font-family:'Open Sans',sans-serif;font-weight:600;font-size:13.5px;color:var(--white)}
.nav-links span{margin-right:47px}
.nav-cta{left:912px;top:53px;width:188px;height:48px;background:var(--slate);color:var(--white);font-family:'Open Sans',sans-serif;font-weight:700;font-size:13.5px;display:flex;align-items:center;justify-content:center}

/* hero */
.hero{top:101px;left:0;width:1200px;height:654px;background:radial-gradient(ellipse at 78% 45%,#7a5a42 0%,#3f3026 35%,#241d18 70%,#1a1512 100%)}
.hero-kicker{left:114px;top:283px;color:var(--white);font-family:'Open Sans',sans-serif;font-weight:700;font-size:16px}
.hero-title{left:113px;top:330px;color:var(--white);font-size:64px}
.hero-text{left:114px;top:421px;width:520px;color:var(--white);font-size:16.5px;line-height:32px}

/* about */
.about-photo{left:110px;top:755px;width:430px;height:501px;background:linear-gradient(160deg,#8a7560 0%,#4a4036 50%,#4f6a30 85%,#5f8a2a 100%)}
.about-deco{left:670px;top:775px;width:500px;height:481px;background:radial-gradient(ellipse at 50% 40%,#f0f0f0,rgba(255,255,255,0) 70%)}
.about-title{left:698px;top:870px;font-size:52px}
.about-text{left:698px;top:934px;width:390px;font-size:14px;line-height:26px;color:var(--muted)}
.about-text p{margin-bottom:13px}

/* services */
.services{top:1256px;left:0;width:1200px;height:775px;background:var(--mint)}
.section-title{left:0;width:1200px;text-align:center;font-size:52px}
.services-intro{left:285px;top:1422px;width:630px;text-align:center;font-family:'Open Sans',sans-serif;font-size:14px;line-height:26px;color:#444}
.card{position:absolute;top:1510px;width:258px;height:338px}
.card-shade{position:absolute;left:0;bottom:0;width:100%;height:120px;background:linear-gradient(rgba(0,0,0,0),rgba(0,0,0,.78))}
.card-icon{position:absolute;left:113px;top:208px;width:32px;height:32px;border-radius:50%;background:var(--green)}
.card-title{position:absolute;left:0;top:250px;width:100%;text-align:center;color:var(--white);font-family:'Open Sans',sans-serif;font-weight:700;font-size:13.5px}
.card-text{position:absolute;left:20px;top:274px;width:218px;text-align:center;color:var(--white);font-size:13.5px;line-height:26px}
.slider-arrow{position:absolute;width:48px;height:48px;border-radius:50%;background:var(--white);box-shadow:0 2px 6px rgba(0,0,0,.25);display:flex;align-items:center;justify-content:center}

/* why */
.why{top:2031px;left:0;width:1200px;height:479px;background:radial-gradient(ellipse at 30% 40%,#56747f,#3d5a66 60%,#35525e)}
.why-item{position:absolute;top:2230px;width:240px;text-align:center;color:var(--white)}
.why-item svg{display:block;margin:0 auto}
.why-item h3{font-family:'Roboto',sans-serif;font-weight:500;font-size:17px;margin-top:26px}
.why-item p{font-size:13.5px;line-height:26px;margin-top:14px}

/* testimonials */
.testi-card{left:192px;top:2743px;width:817px;height:241px;background:#f2f2f2;border-radius:26px}
.testi-avatar{left:561px;top:2703px;width:74px;height:74px;border-radius:50%;background:linear-gradient(135deg,#c9b7a3,#6d6258);border:3px solid var(--white)}
.testi-name{left:192px;top:2810px;width:817px;text-align:center;font-size:13.5px;font-weight:500}
.testi-text{left:250px;top:2846px;width:700px;text-align:center;font-size:13.5px;line-height:31px;color:#555;font-weight:300}
.round-arrow{position:absolute;width:42px;height:42px;border-radius:50%;background:var(--slate);display:flex;align-items:center;justify-content:center}

/* contact */
.contact{top:3090px;left:0;width:1200px;height:570px;background:var(--mint)}
.field{position:absolute;background:var(--white);font-size:12.5px;color:#555;padding:24px 17px}

/* footer */
.footer{top:3660px;left:0;width:1200px;height:342px;background:var(--black);color:var(--white)}
.footer-brand{left:0;top:3742px;width:1200px;display:flex;justify-content:center;align-items:center;gap:12px}
.footer-brand .brand-name{color:var(--white)}
.footer-nav{left:0;top:3827px;width:1200px;display:flex;justify-content:center;gap:45px;font-family:'Open Sans',sans-serif;font-weight:700;font-size:13.5px;color:var(--white)}
.footer-contact{left:0;top:3875px;width:1200px;display:flex;justify-content:center;gap:64px;font-family:'Open Sans',sans-serif;font-weight:700;font-size:16px;color:var(--white)}
.footer-contact div{display:flex;align-items:center;gap:11px}
.copyright{left:0;top:3936px;width:1200px;text-align:center;font-size:10px;color:var(--white)}
</style>
</head>
<body>

<!-- Header -->
<header class="abs site-header">
  <div class="abs brand"><div class="brand-square"></div><div class="brand-name">Verdell Tree Care</div></div>
  <div class="abs top-phone">
    <div class="icon-box"><svg width="15" height="15" viewBox="0 0 24 24"><path fill="#fff" d="M6.6 10.8c1.4 2.8 3.8 5.1 6.6 6.6l2.2-2.2c.3-.3.7-.4 1-.2 1.1.4 2.3.6 3.6.6.6 0 1 .4 1 1V20c0 .6-.4 1-1 1C10.6 21 3 13.4 3 4c0-.6.4-1 1-1h3.5c.6 0 1 .4 1 1 0 1.3.2 2.5.6 3.6.1.3 0 .7-.2 1z"/></svg></div>
    <span>(555) 214 - 0387</span>
  </div>
  <svg class="abs nav-bar" width="825" height="48" viewBox="0 0 825 48"><polygon points="28,0 825,0 825,48 0,48" fill="#8dc63f"/></svg>
  <nav class="abs nav-links"><span>HOME</span><span>ABOUT</span><span>SERVICES</span><span>BLOG</span><span>CONTACT</span></nav>
  <div class="abs nav-cta">GET A FREE ESTIMATE</div>
</header>

<!-- Hero -->
<section class="abs hero" role="img" aria-label="Hands cupping dark soil with a young green seedling"></section>
<div class="abs hero-kicker">WELCOME TO</div>
<h1 class="abs heading hero-title">Verdell <span class="accent">Tree</span> Care</h1>
<p class="abs hero-text">Lorem ipsum dolor sit amet, consectetur adipiscing elit, sed do eiusmod tempor incididunt ut labore et dolore</p>
<div class="btn" style="left:115px;top:508px">Get Started</div>

<!-- About -->
<div class="abs about-deco" role="img" aria-label="Faint silhouette of a tree with a climbing arborist"></div>
<div class="abs about-photo" role="img" aria-label="Arborist in a cap beside a neatly trimmed shrub"></div>
<h2 class="abs heading about-title"><span class="accent">About</span> Us</h2>
<div class="abs about-text">
  <p>Sed ut perspiciatis unde omnis iste natus error sit voluptatem accusantium doloremque laudantium, totam rem aperiam, eaque ipsa quae ab illo inventore veritatis et quasi architecto beatae vitae dicta sunt explicabo. Nemo enim ipsam</p>
  <p>Sed ut perspiciatis unde omnis iste natus error sit voluptatem accusantium doloremque laudantium,</p>
</div>
<div class="btn" style="left:698px;top:1121px">View More</div>

<!-- Services -->
<section class="abs services"></section>
<h2 class="abs heading section-title" style="top:1353px"><span class="accent">Our</span> Services</h2>
<p class="abs services-intro">Lorem ipsum dolor sit amet, consectetur adipiscing elit, sed do eiusmod tempor incididunt ut labore et dolore magna aliqua. Ut enim ad minim</p>

<div class="card" style="left:61px;background:linear-gradient(#b9c2c4,#6f7a5e 55%,#4a5138)" role="img" aria-label="Crew clearing fallen trees after a storm">
  <div class="card-shade"></div><div class="card-icon"></div>
  <div class="card-title">EMERGENCY SERVICES</div>
  <div class="card-text">Sed ut perspiciatis unde omnis iste natus error sit</div>
</div>
<div class="card" style="left:335px;background:linear-gradient(#c5ccd2,#7d8478 55%,#3f4b3a)" role="img" aria-label="Arborist pruning branches with loppers">
  <div class="card-shade"></div><div class="card-icon"></div>
  <div class="card-title">TREE PRUNING</div>
  <div class="card-text">Sed ut perspiciatis unde omnis iste natus error sit</div>
</div>
<div class="card" style="left:608px;background:linear-gradient(#6e7a52,#4a6a2a 50%,#2f2a22)" role="img" aria-label="Chainsaw cutting a log on grass">
  <div class="card-shade"></div><div class="card-icon"></div>
  <div class="card-title">TREE REMOVAL</div>
  <div class="card-text">Sed ut perspiciatis unde omnis iste natus error sit</div>
</div>
<div class="card" style="left:882px;background:linear-gradient(#a8b56a,#7d6a48 55%,#3c3226)" role="img" aria-label="Gloved hands planting a young plant">
  <div class="card-shade"></div><div class="card-icon"></div>
  <div class="card-title">TREE PRESERVATION</div>
  <div class="card-text">Sed ut perspiciatis unde omnis iste natus error sit</div>
</div>
<div class="slider-arrow" style="left:36px;top:1650px"><svg width="14" height="14" viewBox="0 0 14 14"><path d="M9 2 4 7l5 5" stroke="#111" stroke-width="2" fill="none"/></svg></div>
<div class="slider-arrow" style="left:1116px;top:1650px"><svg width="14" height="14" viewBox="0 0 14 14"><path d="m5 2 5 5-5 5" stroke="#111" stroke-width="2" fill="none"/></svg></div>
<div class="btn" style="left:510px;top:1881px">View More</div>

<!-- Why choose us -->
<section class="abs why" role="img" aria-label="Faded portrait of an arborist behind a slate overlay"></section>
<h2 class="abs heading section-title" style="top:2128px;color:var(--white)">Why <span class="accent">Choose</span> Us</h2>

<div class="why-item" style="left:102px">
  <svg width="64" height="64" viewBox="0 0 64 64" fill="none" stroke="#fff" stroke-width="2"><rect x="12" y="6" width="34" height="50" rx="2"/><path d="M19 18h20M19 26h20M19 34h12"/><circle cx="46" cy="42" r="9"/><path d="m42 50-2 9 6-3 6 3-2-9"/></svg>
  <h3>LICENSED &amp; INSURED</h3>
  <p>Lorem ipsum dolor sit amet, consectetur adipiscing</p>
</div>
<div class="why-item" style="left:354px">
  <svg width="64" height="64" viewBox="0 0 64 64" fill="none" stroke="#fff" stroke-width="2"><circle cx="32" cy="24" r="16"/><circle cx="32" cy="24" r="10"/><path d="m32 18 2 4 4 .5-3 3 1 4-4-2-4 2 1-4-3-3 4-.5z"/><path d="m22 37-6 20 7-3 4 6 5-14M42 37l6 20-7-3-4 6-5-14"/></svg>
  <h3>PROFFESSIONAL</h3>
  <p>Lorem ipsum dolor sit amet, consectetur adipiscing</p>
</div>
<div class="why-item" style="left:606px">
  <svg width="64" height="64" viewBox="0 0 64 64" fill="none" stroke="#fff" stroke-width="2"><path d="M22 4h20l-4 10H26z"/><path d="M26 14h12"/><circle cx="32" cy="38" r="22"/><path d="M32 32v18m-6-6 6 6 6-6"/><text x="21" y="31" font-family="Roboto,sans-serif" font-size="9" fill="#fff" stroke="none">TAX</text></svg>
  <h3>FREE &nbsp;ESTIMATE</h3>
  <p>Lorem ipsum dolor sit amet, consectetur adipiscing</p>
</div>
<div class="why-item" style="left:857px">
  <svg width="64" height="64" viewBox="0 0 64 64" fill="none" stroke="#fff" stroke-width="2"><path d="M20 30s-9-10-9-16a9 9 0 0 1 18 0c0 6-9 16-9 16z"/><circle cx="20" cy="14" r="3"/><path d="M44 30s-9-10-9-16a9 9 0 0 1 18 0c0 6-9 16-9 16z"/><circle cx="44" cy="14" r="3"/><path d="M32 58s-9-10-9-16a9 9 0 0 1 18 0c0 6-9 16-9 16z"/><circle cx="32" cy="42" r="3"/><path d="M6 52l10-8M58 52l-10-8"/></svg>
  <h3>LOCALLY OWNED</h3>
  <p>Lorem ipsum dolor sit amet, consectetur adipiscing</p>
</div>

<!-- Testimonials -->
<h2 class="abs heading section-title" style="top:2607px"><span class="accent">Our</span> Testimonials</h2>
<div class="abs testi-card"></div>
<div class="abs testi-avatar" role="img" aria-label="Customer portrait"></div>
<div class="abs testi-name">DANA WHITFIELD</div>
<p class="abs testi-text">I would highly recommend Brightpath for SEO and Sight Management. We have seen huge improvement in our rankings since partnering with them. Lena Marsh is a tremendous asset to your organization. Thank you Lena and Brightpath for being a great partner!</p>
<div class="round-arrow" style="left:172px;top:2843px"><svg width="10" height="10" viewBox="0 0 10 10"><path d="M6 2 3 5l3 3" stroke="#fff" stroke-width="1.5" fill="none"/></svg></div>
<div class="round-arrow" style="left:986px;top:2843px"><svg width="10" height="10" viewBox="0 0 10 10"><path d="m4 2 3 3-3 3" stroke="#fff" stroke-width="1.5" fill="none"/></svg></div>

<!-- Contact -->
<section class="abs contact"></section>
<h2 class="abs heading section-title" style="top:3197px"><span class="accent">Contact</span> Us</h2>
<div class="field" style="left:246px;top:3283px;width:330px;height:65px">Name</div>
<div class="field" style="left:246px;top:3358px;width:330px;height:65px">Phone</div>
<div class="field" style="left:246px;top:3433px;width:330px;height:65px">Email</div>
<div class="field" style="left:588px;top:3283px;width:366px;height:215px">Message</div>
<div class="btn" style="left:510px;top:3515px">Submit</div>

<!-- Footer -->
<footer class="abs footer"></footer>
<div class="abs footer-brand"><div class="brand-square" style="width:36px;height:36px"></div><div class="brand-name">Verdell Tree Care</div></div>
<nav class="abs footer-nav"><span>HOME</span><span>ABOUT</span><span>SERVICES</span><span>BLOG</span><span>CONTACT</span></nav>
<div class="abs footer-contact">
  <div><span class="icon-box"><svg width="15" height="15" viewBox="0 0 24 24"><path fill="#fff" d="M6.6 10.8c1.4 2.8 3.8 5.1 6.6 6.6l2.2-2.2c.3-.3.7-.4 1-.2 1.1.4 2.3.6 3.6.6.6 0 1 .4 1 1V20c0 .6-.4 1-1 1C10.6 21 3 13.4 3 4c0-.6.4-1 1-1h3.5c.6 0 1 .4 1 1 0 1.3.2 2.5.6 3.6.1.3 0 .7-.2 1z"/></svg></span>(555) 214 - 0387</div>
  <div><span class="icon-box"><svg width="15" height="12" viewBox="0 0 20 16"><rect x="1" y="1" width="18" height="14" fill="#fff"/><path d="m1 1 9 7 9-7" stroke="#f39200" stroke-width="1.6" fill="none"/></svg></span>info@verdelltreecare.com</div>
</div>
<div class="abs copyright">COPYRIGHT@2024 - ALL RIGHTS BY VERDELL TREE CARE</div>

</body>
</html>
```